Website for new dental office

I am Dr. Colin Ashford and am building a new dental practice. I specialize in general dentistry. I am young and have a higher end dental practice incorporating very new technologies and would like my website to reflect that. As many dental patients are older, the website must be very easy to navigate. I would like patients to be able to request appointments, and will eventually add on patient information forms (the health history, etc, that you normally fill out in the practice) from my practice management software, so leave an area for that.

Industry/Entity Type

Building

```html
<!DOCTYPE html>
<html lang="en">
<head>
<meta charset="utf-8">
<title>Colin Ashford, DDS — Our Services</title>
<link href="https://fonts.googleapis.com/css2?family=Open+Sans:wght@400;600;700&display=swap" rel="stylesheet">
<style>
:root{
  --blue:#1f7fd6;
  --blue-dark:#14508f;
  --nav-top:#2b8be0;
  --nav-bottom:#1a6ec4;
  --nav-active:#165fa8;
  --ink:#333;
  --muted:#4a4a4a;
  --line:#e3e3e3;
  --orange:#f7921e;
  --orange-dark:#f07c10;
}
*{margin:0;padding:0;box-sizing:border-box}
html,body{width:808px;height:1200px;overflow:hidden;background:#fff}
body{font-family:"Open Sans",Arial,sans-serif;color:var(--ink);position:relative}
.header{position:absolute;left:0;top:0;width:808px;height:78px;background:linear-gradient(#e6f0fb,#fff)}
.brand{position:absolute;left:74px;top:24px;font-size:22px;font-weight:600;color:var(--blue);letter-spacing:.2px}
.phone{position:absolute;left:558px;top:24px;display:flex;align-items:center;gap:8px;font-size:18px;color:#333}
.nav{position:absolute;left:0;top:78px;width:808px;height:29px;background:linear-gradient(var(--nav-top),var(--nav-bottom))}
.nav a{position:absolute;top:0;height:29px;line-height:29px;color:#fff;font-size:10.5px;text-decoration:none;text-transform:uppercase}
.nav a.home{font-weight:700}
.nav a.active{background:var(--nav-active);text-align:center}
.nav .sep{position:absolute;top:4px;width:1px;height:21px;background:rgba(255,255,255,.2)}
.hero{position:absolute;left:0;top:107px;width:808px;height:172px;background:linear-gradient(90deg,#e3edf6,#f3f7fb 55%,#eef3f8)}
.hero-photo{position:absolute;left:440px;top:0;width:368px;height:172px;background:linear-gradient(90deg,rgba(238,243,248,0),#d9c3a8 35%,#e8b36a 70%,#eef1f4)}
.hero h1{position:absolute;left:73px;top:42px;font-size:37px;font-weight:400;color:var(--blue-dark);letter-spacing:-.5px}
.hero h1 b{font-weight:700}
.hero p{position:absolute;left:75px;top:97px;width:330px;font-size:13.5px;line-height:18px;color:#222}
.section-title{position:absolute;left:74px;top:297px;font-size:16px;color:var(--blue)}
.section-rule{position:absolute;left:171px;top:308px;width:78px;height:2px;background:var(--blue)}
.section-dots{position:absolute;left:250px;top:308px;width:483px;border-top:1px dotted #aaa}
.card{position:absolute;left:73px;width:660px;height:167px;border:1px solid var(--line);background:#fff}
.card .photo{position:absolute;left:11px;top:13px;width:114px;height:114px}
.card h2{position:absolute;left:143px;top:8px;font-size:16px;font-weight:600;color:var(--blue)}
.card p{position:absolute;left:143px;width:506px;font-size:8.6px;line-height:12.8px;color:var(--muted)}
.card p.first{top:39px}
.card p.second{top:90px}
.btn{position:absolute;left:143px;top:133px;width:57px;height:20px;line-height:20px;text-align:center;background:var(--blue-dark);color:#fff;font-size:8.6px}
.cta{position:absolute;left:74px;top:1080px;width:659px;height:69px;border:1px solid #e6e6e6;border-radius:4px;background:#f5f5f5}
.cta span{position:absolute;left:12px;top:22px;font-size:17px;color:#444}
.cta .request{position:absolute;left:475px;top:14px;width:170px;height:39px;border-radius:2px;background:linear-gradient(var(--orange),var(--orange-dark));color:#fff;font-size:12.5px;font-weight:600;display:flex;align-items:center;padding-left:10px;gap:8px}
.footer{position:absolute;left:0;top:1173px;width:808px;text-align:center;font-size:8.6px;color:#222}
</style>
</head>
<body>
<header class="header">
  <div class="brand">Colin Ashford, DDS</div>
  <div class="phone">
    <svg width="28" height="28" viewBox="0 0 28 28" aria-hidden="true">
      <path d="M7 4c2 0 3 4 4 6s-3 3-2 5 4 5 6 5 2-3 4-2 5 2 5 4-3 4-5 4C11 26 2 17 2 9c0-3 3-5 5-5z" fill="#1f2d3d"/>
      <circle cx="19" cy="10" r="7" fill="#fff" stroke="#1f7fd6" stroke-width="1.6"/>
      <text x="19" y="13" font-size="8" font-weight="700" text-anchor="middle" fill="#1f7fd6" font-family="Open Sans,sans-serif">24</text>
    </svg>
    123 555 0188
  </div>
</header>

<nav class="nav">
  <a class="home" style="left:74px">Home</a>
  <a class="active" style="left:126px;width:88px">Services</a>
  <span class="sep" style="left:214px"></span>
  <a style="left:236px">Resources</a>
  <span class="sep" style="left:305px"></span>
  <a style="left:332px">Portfolio</a>
  <span class="sep" style="left:404px"></span>
  <a style="left:433px">Team</a>
  <span class="sep" style="left:486px"></span>
  <a style="left:505px">Contact</a>
</nav>

<section class="hero">
  <div class="hero-photo" role="img" aria-label="Photo of a smiling family of three"></div>
  <h1>Our <b>Services</b></h1>
  <p>Lorem Ipsum is simply dummy text of the printing and typesetting industry. Lorem Ipsum has been</p>
</section>

<h3 class="section-title">Our Services</h3>
<div class="section-rule"></div>
<div class="section-dots"></div>

<article class="card" style="top:333px">
  <div class="photo" role="img" aria-label="Photo of a smiling woman" style="background:linear-gradient(135deg,#8a4a2e,#e9c2a8 55%,#f3e3d8)"></div>
  <h2>Cosmetics</h2>
  <p class="first">we believe that "prevention is better than cure". That's why we offer an one hour comprehensive oral examination, which includes a virtual tour of your mouth, intra-oral photos, scale and clean, polish, fluoride treatment and X-rays as required, to ensure you are receiving the best care possible.</p>
  <p class="second">We recommend visiting us at least every 6 months for a routine check-up. Combined with appropriate oral hygiene, you can prevent the need for costly treatments in the future.</p>
  <a class="btn">Read More</a>
</article>

<article class="card" style="top:522px">
  <div class="photo" role="img" aria-label="Illustration of a dental bridge on implants" style="background:linear-gradient(#f4f1ee,#e8b7b0 55%,#c96a63)"></div>
  <h2 style="top:4px">Restorative Procedures</h2>
  <p class="first" style="top:35px">we believe that "prevention is better than cure". That's why we offer an one hour comprehensive oral examination, which includes a virtual tour of your mouth, intra-oral photos, scale and clean, polish, fluoride treatment and X-rays as required, to ensure you are receiving the best care possible.</p>
  <p class="second" style="top:86px">We recommend visiting us at least every 6 months for a routine check-up. Combined with appropriate oral hygiene, you can prevent the need for costly treatments in the future.</p>
  <a class="btn" style="left:145px;top:133px">Read More</a>
</article>

<article class="card" style="top:710px">
  <div class="photo" role="img" aria-label="Photo of a woman biting a green apple" style="background:linear-gradient(135deg,#3d2a1e,#b58a6a 45%,#8fb43a 70%,#5a7a2a)"></div>
  <h2 style="left:145px;top:5px">Dental Implants</h2>
  <p class="first" style="left:145px;top:38px">Dental, we believe that "prevention is better than cure". That's why we offer an one hour comprehensive oral examination, which includes a virtual tour of your mouth, intra-oral photos, scale and clean, polish, fluoride treatment and X-rays as required, to ensure you are receiving the best care possible.</p>
  <p class="second" style="left:145px;top:89px">We recommend visiting us at least every 6 months for a routine check-up. Combined with appropriate oral hygiene, you can prevent the need for costly treatments in the future.</p>
  <a class="btn" style="left:143px;top:133px">Read More</a>
</article>

<article class="card" style="top:892px">
  <div class="photo" role="img" aria-label="Illustration of teeth with an implant in the gum" style="top:22px;left:14px;background:linear-gradient(#f5f5f7,#dfe3ea 45%,#f0a4b8)"></div>
  <h2 style="top:6px">Restorative Procedures</h2>
  <p class="first" style="top:39px">l, we believe that "prevention is better than cure". That's why we offer an one hour comprehensive oral examination, which includes a virtual tour of your mouth, intra-oral photos, scale and clean, polish, fluoride treatment and X-rays as required, to ensure you are receiving the best care possible.</p>
  <p class="second" style="top:90px">We recommend visiting us at least every 6 months for a routine check-up. Combined with appropriate oral hygiene, you can prevent the need for costly treatments in the future.</p>
  <a class="btn" style="top:132px">Read More</a>
</article>

<section class="cta">
  <span>Want to Get Treated? Schedule Your Appointment Now!</span>
  <a class="request">Request Appointment
    <svg width="18" height="17" viewBox="0 0 18 17" aria-hidden="true">
      <rect x="1" y="2.5" width="16" height="13.5" rx="1" fill="none" stroke="#3a2a1a" stroke-width="1.3"/>
      <line x1="5" y1="0.5" x2="5" y2="4" stroke="#3a2a1a" stroke-width="1.3"/>
      <line x1="13" y1="0.5" x2="13" y2="4" stroke="#3a2a1a" stroke-width="1.3"/>
      <g fill="#3a2a1a">
        <rect x="4" y="7" width="2" height="2"/><rect x="8" y="7" width="2" height="2"/><rect x="12" y="7" width="2" height="2"/>
        <rect x="4" y="11" width="2" height="2"/><rect x="8" y="11" width="2" height="2"/><rect x="12" y="11" width="2" height="2"/>
      </g>
    </svg>
  </a>
</section>

<footer class="footer">© Copyrights 2014 All rights Reserved</footer>
</body>
</html>
```